Business Card Design Project - 2 sided

We need a business card design for a card having one business on each side (ie. two businesses on one card). Would like a design that incorporates logo, tagline and normal fields (name, position, address, phone).

Would also like an allowance for small font text along the bottom (text to be determined, but less than 50 characters).

NB. Attached logo for Harbor Quill has two variations - either can be used.

www.harborquill-example.com / www.velmaro-example.com

```html
<!DOCTYPE html>
<html lang="en">
<head>
<meta charset="utf-8">
<title>Harbor Quill / Velmaro – Two-sided Business Card</title>
<link href="https://fonts.googleapis.com/css2?family=Source+Sans+3:wght@400;600;700&display=swap" rel="stylesheet">
<style>
  :root {
    --stage: #ececec;
    --card: #ffffff;
    --ink: #555555;
    --rule: #8a8a8a;
    --green: #8cc63f;
    --navy: #2f3777;
    --blue: #3a8fc4;
  }
  * { box-sizing: border-box; margin: 0; padding: 0; }
  html, body {
    width: 1200px; height: 487px; overflow: hidden;
    background: var(--stage);
    font-family: "Source Sans 3", "Myriad Pro", sans-serif;
  }
  .card {
    position: absolute; top: 90px;
    width: 543px; height: 310px;
    background: var(--card);
    border-radius: 14px;
  }
  .card--front { left: 47px; }
  .card--back { left: 612px; }

  .brand { position: absolute; display: flex; align-items: center; gap: 10px; }
  .brand__dot { width: 26px; height: 26px; border-radius: 50%; }
  .brand__name { font-size: 24px; font-weight: 600; line-height: 1; }
  .card--front .brand { left: 44px; top: 82px; }
  .card--front .brand__dot { background: var(--green); }
  .card--front .brand__name { color: var(--navy); letter-spacing: 0.5px; }
  .card--back .brand { left: 38px; top: 62px; }
  .card--back .brand__dot { width: 40px; height: 40px; background: var(--green); }
  .card--back .brand__name { color: var(--blue); font-size: 44px; font-weight: 700; }

  .tagline { position: absolute; color: var(--ink); line-height: 1; }
  .card--front .tagline { left: 44px; top: 114px; font-size: 9.5px; color: #333; }
  .card--back .tagline { left: 108px; top: 108px; font-size: 14.5px; letter-spacing: 0.6px; }

  .rule { position: absolute; top: 130px; height: 1px; background: var(--rule); }
  .rule--lead { left: 0; width: 335px; }
  .rule--tail { left: 510px; width: 33px; }

  .person {
    position: absolute; top: 116px; left: 342px;
    font-size: 16.5px; color: var(--ink); white-space: nowrap;
  }
  .person__name { color: var(--green); font-weight: 700; }

  .contacts {
    position: absolute; right: 40px; top: 149px;
    list-style: none; text-align: right;
    font-size: 13.5px; color: var(--ink);
  }
  .contacts li { height: 17.8px; display: flex; justify-content: flex-end; align-items: center; gap: 4px; }
  .contacts svg { width: 10px; height: 10px; }

  .address {
    position: absolute; right: 42px; top: 244px;
    font-size: 14px; color: var(--ink);
  }
  .fineprint {
    position: absolute; right: 42px; top: 268px;
    font-size: 10.5px; color: var(--ink); letter-spacing: -0.2px;
  }
</style>
</head>
<body>
<svg width="0" height="0" style="position:absolute">
  <defs>
    <symbol id="i-phone" viewBox="0 0 10 10"><circle cx="5" cy="5" r="5" fill="#8cc63f"/><path d="M3 2.5 L4.2 3.8 3.7 4.5 Q4.5 5.9 5.5 6.3 L6.2 5.8 7.5 7 6.8 7.8 Q3.5 7.5 2.3 3.2Z" fill="#fff"/></symbol>
    <symbol id="i-mobile" viewBox="0 0 10 10"><rect x="2.5" y="0.5" width="5" height="9" rx="1" fill="#8cc63f"/><rect x="3.4" y="1.6" width="3.2" height="4" fill="#fff"/></symbol>
    <symbol id="i-fax" viewBox="0 0 10 10"><rect x="0.5" y="3" width="9" height="6" rx="1" fill="#8cc63f"/><rect x="2.5" y="0.8" width="5" height="3" fill="#8cc63f"/><rect x="2.5" y="5.3" width="5" height="1.2" fill="#fff"/></symbol>
    <symbol id="i-mail" viewBox="0 0 10 10"><circle cx="5" cy="5" r="5" fill="#8cc63f"/><rect x="2.2" y="3.2" width="5.6" height="3.8" fill="#fff"/><path d="M2.2 3.2 L5 5.4 7.8 3.2" stroke="#8cc63f" stroke-width="0.7" fill="none"/></symbol>
    <symbol id="i-web" viewBox="0 0 10 10"><circle cx="5" cy="5" r="5" fill="#8cc63f"/><path d="M1 5 H9" stroke="#fff" stroke-width="0.8"/></symbol>
  </defs>
</svg>

<section class="card card--front">
  <div class="brand"><span class="brand__dot"></span><span class="brand__name">Harbor Quill</span></div>
  <p class="tagline">Website Translation and Localisation Specialist...</p>
  <div class="rule rule--lead"></div>
  <p class="person"><span class="person__name">YOUR NAME</span> / Title</p>
  <div class="rule rule--tail"></div>
  <ul class="contacts">
    <li>123-456-7890 <svg><use href="#i-phone"/></svg></li>
    <li>123-456-7890 <svg><use href="#i-mobile"/></svg></li>
    <li>123-456-7890 <svg><use href="#i-fax"/></svg></li>
    <li>name@website.com <svg><use href="#i-mail"/></svg></li>
    <li>www.website.com <svg><use href="#i-web"/></svg></li>
  </ul>
  <p class="address">Complex name, Street City, State, zip code</p>
  <p class="fineprint">xxxxxxxxxxxxxxxxxxxxxxxxxxxxxxxxxxxxxxxxxxxxxxxxxxx</p>
</section>

<section class="card card--back">
  <div class="brand"><span class="brand__dot"></span><span class="brand__name">Velmaro</span></div>
  <p class="tagline">Professional SEO Services</p>
  <div class="rule rule--lead"></div>
  <p class="person"><span class="person__name">YOUR NAME</span> / Title</p>
  <div class="rule rule--tail"></div>
  <ul class="contacts">
    <li>123-456-7890 <svg><use href="#i-phone"/></svg></li>
    <li>123-456-7890 <svg><use href="#i-mobile"/></svg></li>
    <li>123-456-7890 <svg><use href="#i-fax"/></svg></li>
    <li>name@website.com <svg><use href="#i-mail"/></svg></li>
    <li>www.website.com <svg><use href="#i-web"/></svg></li>
  </ul>
  <p class="address">Complex name, Street City, State, zip code</p>
  <p class="fineprint">xxxxxxxxxxxxxxxxxxxxxxxxxxxxxxxxxxxxxxxxxxxxxxxxxxx</p>
</section>
</body>
</html>
```